Business Cards for new orthopaedic surgery practice

My husband and I are starting our own orthopaedic surgery practice. We are looking for a business card that is uniform, but one will have my name/title and the other will have his. You can just create one design with my name on it for now. But when I choose your design as the winning design I will ask that you add another copy with his name/title.

We are looking for classy, simple, elite all in one. We like dark blues/a little gold/yellow. Something that goes with our logo. We want our logo incorporated. Here is all the info you need:
Business name: RV Bone & Vitality Center
Location: 38517 North Willowmere Ave
Maple Hollow, FL 33418
Phone: 954-218-4063
Fax: 954-582-7341
Email: info@myrvbonecare.example

Names: Lydia Vance, M.D.
Board Certified Hand and Upper Extremity Surgeon

Ebo Dansu, M.D.
Board Certified Hip & Knee Replacement/General Orthopaedic Surgeon

Can decide what you want to put on the back. Maybe a slogan:
Grounded in Care. Centered on You

I am just going to upload our logo. The only thing is if we select you as the winning design, the location, and phone numbers may change. We will need your help to update that once fully solidified.

Industry/Entity Type

Medical

Contact Information for Business Card

Colors
0054AA
0677BA
7BADD7
CADEEF
E8F1F8
0094D4
00A9DD
6FCCEA
C7EBF8
E9F6FB

Requirements
Must have
• class, appeal,
Should not have
• We want to air on the side of masculine if we are looking at masculine vs. feminine feel. But we still want it classy, sophisticated, and something we will love

```html
<!DOCTYPE html>
<html lang="en">
<head>
<meta charset="utf-8">
<title>RV Bone &amp; Vitality Center — Business Cards</title>
<link rel="stylesheet" href="https://fonts.googleapis.com/css2?family=Tinos:wght@400;700&display=swap">
<style>
  :root {
    --navy: #1c2951;
    --navy-raised: #2b3b6b;
    --gold: #c9a45e;
    --white: #ffffff;
    --ink: #111111;
    --stage: #e4e5e8;
  }
  * { box-sizing: border-box; margin: 0; padding: 0; }
  html, body { width: 1200px; height: 694px; overflow: hidden; }
  body {
    background: var(--stage);
    font-family: "Tinos", "Times New Roman", serif;
    display: flex;
    align-items: center;
    justify-content: center;
    gap: 40px;
  }
  .card {
    position: relative;
    width: 540px;
    height: 308px;
    border-radius: 22px;
    overflow: hidden;
    box-shadow: 0 6px 18px rgba(0,0,0,.18);
  }

  /* Back */
  .card-back { background: var(--navy); }
  .back-mark {
    position: absolute;
    left: 50%; top: 36px;
    transform: translateX(-50%);
    width: 150px; height: 150px;
    border: 2px solid var(--navy-raised);
    border-radius: 50%;
    display: flex; align-items: center; justify-content: center;
    text-align: center;
    color: var(--navy-raised);
    font-size: 17px;
    line-height: 1.25;
    padding: 18px;
  }
  .slogan {
    position: absolute;
    left: 0; right: 0; bottom: 62px;
    text-align: center;
    color: var(--white);
    font-size: 27px;
    letter-spacing: .5px;
  }

  /* Front */
  .card-front { background: var(--white); }
  .gold-panel { position: absolute; inset: 0; width: 100%; height: 100%; }
  .front-mark {
    position: absolute;
    left: 52px; top: 56px;
    width: 200px; height: 200px;
    border: 3px solid var(--navy);
    border-radius: 50%;
    display: flex; align-items: center; justify-content: center;
    text-align: center;
    color: var(--navy);
    font-weight: 700;
    font-size: 24px;
    line-height: 1.2;
    padding: 24px;
  }
  .details {
    position: absolute;
    right: 30px; top: 34px;
    text-align: right;
    color: var(--ink);
  }
  .doctor-name {
    color: var(--navy);
    font-weight: 700;
    font-size: 27px;
    line-height: 1.1;
  }
  .doctor-title {
    color: var(--navy);
    font-size: 14.5px;
    line-height: 1.25;
    margin-top: 4px;
  }
  .contact-list { list-style: none; margin-top: 16px; font-size: 15px; line-height: 1.55; }
  .contact-list li { display: flex; align-items: center; justify-content: flex-end; gap: 8px; }
  .contact-icon { width: 14px; height: 14px; fill: var(--gold); }
  .address { margin-top: 14px; font-size: 15px; line-height: 1.4; padding-right: 22px; }
</style>
</head>
<body>

  <section class="card card-back" aria-label="Business card back">
    <div class="back-mark">RV Bone &amp; Vitality Center</div>
    <p class="slogan">Grounded in Care. Centered on You</p>
  </section>

  <section class="card card-front" aria-label="Business card front">
    <svg class="gold-panel" viewBox="0 0 540 308" preserveAspectRatio="none" aria-hidden="true">
      <polygon points="0,0 148,0 262,308 0,308" fill="var(--gold)"/>
    </svg>
    <div class="front-mark">RV Bone &amp; Vitality Center</div>

    <div class="details">
      <h1 class="doctor-name">Lydia Vance, M.D.</h1>
      <p class="doctor-title">Board Certified Hand and<br>Upper Extremity Surgeon</p>
      <ul class="contact-list">
        <li>954-218-4063
          <svg class="contact-icon" viewBox="0 0 24 24" aria-label="Phone"><path d="M6.6 10.8a15.1 15.1 0 0 0 6.6 6.6l2.2-2.2a1 1 0 0 1 1-.25 11.4 11.4 0 0 0 3.6.57 1 1 0 0 1 1 1V20a1 1 0 0 1-1 1A17 17 0 0 1 3 4a1 1 0 0 1 1-1h3.5a1 1 0 0 1 1 1c0 1.25.2 2.45.57 3.57a1 1 0 0 1-.25 1z"/></svg>
        </li>
        <li>954-582-7341
          <svg class="contact-icon" viewBox="0 0 24 24" aria-label="Fax"><path d="M6 2h9l3 3v5H6z M3 10h18a1 1 0 0 1 1 1v10a1 1 0 0 1-1 1H3a1 1 0 0 1-1-1V11a1 1 0 0 1 1-1z M13 13v2h2v-2z m4 0v2h2v-2z m-4 4v2h2v-2z m4 0v2h2v-2z" fill-rule="evenodd"/></svg>
        </li>
      </ul>
      <p class="address">38517 North Willowmere Ave<br>Maple Hollow, FL 33418</p>
    </div>
  </section>

</body>
</html>
```